770 76 Chiro Brochure

https://files.vornaledge.net/sheet/q/84TxRm_wLz-Kq_PYbnHcVe391zd_4RQlmJTsPAk92x6/view?src=link

Brochure to show chiropractors about our program

```html
<!DOCTYPE html>
<html lang="en">
<head>
<meta charset="utf-8">
<title>76-SPINE Billboard Program Brochure</title>
<link rel="stylesheet" href="https://fonts.googleapis.com/css2?family=Anton&family=Poppins:wght@400;500;600;700;800&display=swap">
<style>
  :root {
    --navy: #0d3b84;
    --navy-deep: #072a63;
    --sky-top: #0b3a80;
    --sky-mid: #2f6fc0;
    --sky-low: #9cc6ea;
    --grass: #4f9a2c;
    --grass-dark: #2f6b19;
    --yellow: #f6c90e;
    --red: #e1251b;
    --lime: #e3dc4b;
    --board-dark: #0f1a10;
    --board-green: #1f3a1c;
    --green: #4aa23b;
    --green-bar: #1f9a3a;
    --ink: #1b1b1b;
    --white: #ffffff;
    --canvas: #e4e4e4;
  }
  * { box-sizing: border-box; margin: 0; padding: 0; }
  html, body { width: 870px; height: 1200px; overflow: hidden; }
  body {
    background: var(--canvas);
    font-family: "Poppins", sans-serif;
    color: var(--ink);
    display: flex;
    align-items: center;
    justify-content: center;
    gap: 18px;
  }
  .page {
    position: relative;
    width: 416px;
    height: 590px;
    overflow: hidden;
    box-shadow: 0 4px 14px rgba(0,0,0,.18);
  }

  /* ---------- Front ---------- */
  .page-front { color: var(--white); }
  .front-scene {
    position: absolute; inset: 0;
    background: linear-gradient(180deg, var(--sky-top) 0%, var(--sky-mid) 38%, var(--sky-low) 74%, #d8ecf7 80%, var(--grass) 82%, var(--grass-dark) 100%);
  }
  .front-title {
    position: absolute; top: 22px; left: 0; right: 0;
    text-align: center;
    font-family: "Anton", sans-serif;
    line-height: 1;
  }
  .front-title .line-1 { font-size: 62px; letter-spacing: 1px; display: block; }
  .front-title .line-2 { font-size: 44px; letter-spacing: 0.5px; display: block; margin-top: 2px; }
  .front-ribbon {
    position: absolute; top: 136px; left: 27px; width: 362px; height: 40px;
    background: var(--yellow);
    border: 2px solid #1b1b1b;
    border-radius: 8px;
    display: flex; align-items: center; justify-content: center; gap: 8px;
    color: var(--ink);
    font-weight: 800; font-size: 24px; letter-spacing: 0.3px;
  }
  .front-ribbon::before, .front-ribbon::after {
    content: ""; width: 20px; height: 2px; background: var(--ink);
  }
  .front-partner {
    position: absolute; top: 196px; left: 0; right: 0;
    text-align: center; font-size: 13px; line-height: 1.35;
  }
  .front-partner strong { font-weight: 700; display: block; }
  .front-board { position: absolute; top: 243px; left: 24px; font-size: 9.9px; }

  /* ---------- Billboard component ---------- */
  .board {
    position: relative;
    width: 37.6em; height: 14em;
    background: radial-gradient(circle at 72% 40%, var(--board-green) 0%, var(--board-dark) 70%);
    border: 0.15em solid #d9d9d9;
    overflow: hidden;
    color: var(--white);
  }
  .board-copy { position: absolute; left: 1.5em; top: 0.9em; width: 26em; }
  .board-headline { font-family: "Anton", sans-serif; line-height: 1; white-space: nowrap; }
  .board-headline .injured { color: var(--red); font-size: 3em; }
  .board-headline .accident { color: var(--lime); font-size: 1.8em; margin-left: 0.15em; }
  .board-call { display: flex; align-items: center; gap: 0.5em; margin-top: 0.35em; }
  .board-call .call-now {
    font-family: "Poppins", sans-serif; font-weight: 800; color: var(--yellow);
    font-size: 1.4em; line-height: 0.95;
  }
  .board-call .phone { font-family: "Anton", sans-serif; font-size: 3.7em; line-height: 1; white-space: nowrap; }
  .board-tagline { font-size: 0.95em; letter-spacing: 0.04em; margin-top: 0.3em; white-space: nowrap; }
  .board-tagline span { padding: 0 0.4em; }
  .board-footer { display: flex; align-items: center; gap: 1.2em; margin-top: 0.7em; }
  .board-clinic { font-size: 1.25em; font-weight: 500; color: var(--lime); white-space: nowrap; }
  .board-clinic small { display: block; font-size: 0.45em; color: var(--white); letter-spacing: 0.05em; }
  .board-tag {
    background: var(--yellow); color: var(--ink);
    font-weight: 800; font-size: 1.55em; line-height: 1;
    padding: 0.3em 1.6em 0.3em 0.7em;
    clip-path: polygon(0 0, 100% 0, 88% 100%, 0 100%);
    white-space: nowrap;
  }
  .board-photo {
    position: absolute; right: 0; bottom: 0; width: 12em; height: 13.6em;
    background: linear-gradient(180deg, #3a4a3a 0%, #6b7a86 55%, #2c3440 100%);
  }

  /* ---------- Back ---------- */
  .page-back {
    background: var(--white);
    padding: 13px 16px 0;
    display: flex; flex-direction: column;
  }
  .heading-yellow {
    background: var(--yellow); border-radius: 6px;
    color: var(--navy-deep); font-weight: 700; font-size: 11.4px;
    text-align: center; padding: 4px 0;
  }
  .benefit-list { list-style: none; margin: 8px 0 0 4px; }
  .benefit-list li {
    display: flex; gap: 8px; align-items: flex-start;
    font-size: 7.6px; line-height: 1.4; margin-bottom: 7px;
  }
  .benefit-list svg { flex: none; width: 15px; height: 13px; }
  .heading-navy {
    background: var(--navy); border-radius: 6px; color: var(--white);
    font-weight: 700; font-size: 11.5px; text-align: center; padding: 4px 0;
    display: flex; align-items: center; justify-content: center; gap: 10px;
  }
  .heading-navy::before, .heading-navy::after { content: ""; width: 32px; height: 1.5px; background: var(--white); }
  .feature-row { display: flex; margin: 9px 0 10px; }
  .feature {
    flex: 1; display: flex; align-items: center; gap: 8px;
    font-size: 7.8px; font-weight: 500; line-height: 1.3;
    padding: 0 4px;
  }
  .feature + .feature { border-left: 1px solid #cfcfcf; padding-left: 10px; }
  .feature-icon {
    flex: none; width: 42px; height: 42px; border-radius: 50%;
    background: var(--green); border: 2px solid #cfe6c9;
    display: flex; align-items: center; justify-content: center;
  }
  .feature-icon svg { width: 20px; height: 20px; }
  .heading-bar {
    background: var(--navy); color: var(--white);
    font-weight: 700; font-size: 9px; padding: 2px 8px;
  }
  .body-copy { font-size: 7.6px; line-height: 1.42; margin: 5px 0 8px; text-align: justify; }
  .town-list { font-size: 7.6px; line-height: 1.45; margin: 5px 0 9px; }
  .board-grid {
    display: grid; grid-template-columns: 1fr 1fr; gap: 5px 4px;
    font-size: 4.9px;
  }
  .board-grid .board-clinic { font-size: 1.6em; }
  .back-bar { margin: auto -16px 0; height: 10px; background: var(--green-bar); }
</style>
</head>
<body>

  <section class="page page-front" aria-label="Brochure front">
    <div class="front-scene" role="img" aria-label="Photo of a billboard on a tall pole over a green field with wind turbines under a blue sky"></div>
    <h1 class="front-title">
      <span class="line-1">CHIROPRACTIC</span>
      <span class="line-2">BILLBOARD PROGRAM</span>
    </h1>
    <div class="front-ribbon">PERSONAL INJURY</div>
    <p class="front-partner">WE PARTNER WITH <strong>GEORGIA CHIROPRACTORS.</strong></p>

    <div class="front-board">
      <div class="board">
        <div class="board-photo" role="img" aria-label="Portrait photo of a smiling chiropractor"></div>
        <div class="board-copy">
          <div class="board-headline"><span class="injured">INJURED</span><span class="accident">IN A CAR ACCIDENT?</span></div>
          <div class="board-call"><span class="call-now">CALL<br>NOW</span><span class="phone">(555) 76-SPINE</span></div>
          <div class="board-tagline">SAME DAY APPOINTMENTS<span>|</span>LOCATIONS ACROSS GEORGIA</div>
          <div class="board-footer">
            <div class="board-clinic">Oakline Rehab<small>AUTO INJURY CHIROPRACTIC</small></div>
            <div class="board-tag">HABLA ESPANOL</div>
          </div>
        </div>
      </div>
    </div>
  </section>

  <section class="page page-back" aria-label="Brochure back">
    <h2 class="heading-yellow">HOW TO DOMINATE PERSONAL INJURY ADVERTISING</h2>
    <ul class="benefit-list">
      <li><svg viewBox="0 0 16 14"><path d="M1 7.5l4.5 4.5L15 1.5" fill="none" stroke="#1f9a3a" stroke-width="3" stroke-linecap="round" stroke-linejoin="round"/></svg><span><b>(555) 76-SPINE</b> is the preeminent vanity phone number for Chiropractors in Georgia to dominate personal injury advertising.</span></li>
      <li><svg viewBox="0 0 16 14"><path d="M1 7.5l4.5 4.5L15 1.5" fill="none" stroke="#1f9a3a" stroke-width="3" stroke-linecap="round" stroke-linejoin="round"/></svg><span><b>(555) 76-SPINE</b> is more valuable than ever because of digital advertising.</span></li>
      <li><svg viewBox="0 0 16 14"><path d="M1 7.5l4.5 4.5L15 1.5" fill="none" stroke="#1f9a3a" stroke-width="3" stroke-linecap="round" stroke-linejoin="round"/></svg><span>See how <b>(555) 76-SPINE</b> proved to substantially increase ROI through the SearchPoint Ads Algorithm and increase your SearchPoint Quality Score.</span></li>
    </ul>

    <h2 class="heading-navy">EVERY BILLBOARD WE CREATE INCLUDES</h2>
    <div class="feature-row">
      <div class="feature">
        <span class="feature-icon"><svg viewBox="0 0 20 20"><rect x="2" y="2" width="16" height="16" rx="3" fill="none" stroke="#fff" stroke-width="1.8"/><path d="M10 6v8M6 10h8" stroke="#fff" stroke-width="2.2" stroke-linecap="round"/></svg></span>
        <span>Chiropractors<br>Doctors<br>Photo</span>
      </div>
      <div class="feature">
        <span class="feature-icon"><svg viewBox="0 0 20 20"><rect x="2" y="4" width="13" height="13" fill="none" stroke="#fff" stroke-width="1.8"/><path d="M8 12l9-9 1.5 1.5-9 9H8z" fill="#fff"/></svg></span>
        <span>Your Brand /<br>Logo on the<br>billboards</span>
      </div>
      <div class="feature">
        <span class="feature-icon"><svg viewBox="0 0 20 20"><path d="M4 2.5l3 .2 1.3 3.6-1.9 1.4a10 10 0 0 0 5.9 5.9l1.4-1.9 3.6 1.3.2 3c-.1.8-.8 1.5-1.6 1.5C8.6 17.5 2.5 11.4 2.5 4.1c0-.8.7-1.5 1.5-1.6z" fill="#fff"/><circle cx="12" cy="5" r="1.1" fill="#fff"/><circle cx="15" cy="5" r="1.1" fill="#fff"/><circle cx="12" cy="8" r="1.1" fill="#fff"/><circle cx="15" cy="8" r="1.1" fill="#fff"/></svg></span>
        <span>Direct dial<br>forwarded to<br>your office</span>
      </div>
    </div>

    <h3 class="heading-bar">REACH NEW CLIENTS / PATIENTS IN A BIG WAY!</h3>
    <p class="body-copy">Expand your marketing mix and grow your business through our professionally designed billboards that showcase your photo, name, logo, at any time and in any place. Billboards set you apart from the competition by building credibility and brand recognition. Billboards serve as an important top-of-funnel channel and in conjunction with your current marketing channels, will increase your effectiveness.</p>

    <h3 class="heading-bar">GEORGIA BILLBOARD LOCATIONS (OVER 200 BOARDS AVAILABLE)</h3>
    <p class="town-list">Albany - Athens - Atlanta - Augusta - Blairville - Blackshear - Blue Ridge - Conyers - Valdosta Cummings - Dalton - Ft Oglethorpe - Hazelhurst - Jesup - Kennesaw - Macon - McDonough Savannah - Thomasville - Toccoa - Young Harris - Watkinsville - Bogart - Winder - Sandersville Tifton - Cordele - Clayton - Milledgeville - Dublin - Chatsworth - Mineral Bluff - Eatonsville Hinesville - Warner Robins - Moultrie - LaFayette - Senoia - Ackworth - Camilla - Dawsonville Barnesville - Bainbridge - Cairo - Americus</p>

    <div class="board-grid">
      <div class="board">
        <div class="board-photo" role="img" aria-label="Photo of two chiropractors in blue scrubs"></div>
        <div class="board-copy">
          <div class="board-headline"><span class="injured">INJURED</span><span class="accident">IN A CAR ACCIDENT?</span></div>
          <div class="board-call"><span class="call-now">CALL<br>NOW</span><span class="phone">(555) 76-SPINE</span></div>
          <div class="board-tagline">SAME DAY APPOINTMENTS<span>|</span>LOCATIONS ACROSS GEORGIA</div>
          <div class="board-footer">
            <div class="board-clinic">Metro Spine<small>DR. MARA LIND, D.C. &amp; DR. OWEN HALE, D.C.</small></div>
            <div class="board-tag">NECK &amp; BACK PAIN</div>
          </div>
        </div>
      </div>
      <div class="board">
        <div class="board-photo" role="img" aria-label="Photo of a chiropractor in a white coat"></div>
        <div class="board-copy">
          <div class="board-headline"><span class="injured">INJURED</span><span class="accident">IN A CAR ACCIDENT?</span></div>
          <div class="board-call"><span class="call-now">CALL<br>NOW</span><span class="phone">(555) 76-SPINE</span></div>
          <div class="board-tagline">SAME DAY APPOINTMENTS<span>|</span>LOCATIONS ACROSS GEORGIA</div>
          <div class="board-footer">
            <div class="board-clinic">Calmway</div>
            <div class="board-tag">NECK &amp; BACK PAIN</div>
          </div>
        </div>
      </div>
      <div class="board">
        <div class="board-photo" role="img" aria-label="Photo of a chiropractor in a white coat"></div>
        <div class="board-copy">
          <div class="board-headline"><span class="injured">INJURED</span><span class="accident">IN A CAR ACCIDENT?</span></div>
          <div class="board-call"><span class="call-now">CALL<br>NOW</span><span class="phone">(555) 76-SPINE</span></div>
          <div class="board-tagline">SAME DAY APPOINTMENTS<span>|</span>LOCATIONS ACROSS GEORGIA</div>
          <div class="board-footer">
            <div class="board-clinic">Calmway</div>
            <div class="board-tag">NECK &amp; BACK PAIN</div>
          </div>
        </div>
      </div>
      <div class="board">
        <div class="board-photo" role="img" aria-label="Photo of a chiropractor in a white coat"></div>
        <div class="board-copy">
          <div class="board-headline"><span class="injured">INJURED</span><span class="accident">IN A CAR ACCIDENT?</span></div>
          <div class="board-call"><span class="call-now">CALL<br>NOW</span><span class="phone">(555) 76-SPINE</span></div>
          <div class="board-tagline">SAME DAY APPOINTMENTS<span>|</span>LOCATIONS ACROSS GEORGIA</div>
          <div class="board-footer">
            <div class="board-clinic">Clinica Sereno</div>
            <div class="board-tag">HABLA ESPANOL</div>
          </div>
        </div>
      </div>
    </div>

    <div class="back-bar"></div>
  </section>

</body>
</html>
```